Audio Visual company needs WordPress Site re-design

We need a new, simple and sleek redesign of our website, www.kelvarosupply.net. It is crucial that it is mobile platform friendly! The company emphasis is on commercial sound and video installation.

Examples of what our company does can be found here: http://bramwickav.org/

I am NOT looking for a storefront or an e-commerce site. I would just like an elegant site that describes our services. Perhaps incorporate a sleek showcase into the homepage of projects we have completed. Also would like an elegant menu-bar, perhaps enhance our current site menu or similar.

Here is a link to another site that exhibits the content I am looking for. Their target market is also much like mine.
http://www.pollanderhouse.com/ ........ A polished up version of this site would probably be my ideal site. It has almost EXACTLY the content I am looking for. Exclude the "Printing & signage" category. Needs nicer menus, contact page and project showcase.

Here is another example: http://www.clearhavenmedia.com/ ......... This site has a very nice homepage design with a good layout and feature slider. The site is simple, elegant and to the point.

Target Market(s)

Corporate/commercial business, Educational institutions

Industry/Entity Type

E-Commerce

Font styles to use
Serif
Sans Serif

Requirements
Must have
• Mobile friendly navigation
Nice to have
• HTML5 & CSS3
Should not have
• No Adobe Flash content. No store templates or e-commerce. We are a service based company not a product sales company

```html
<!DOCTYPE html>
<html lang="en">
<head>
<meta charset="utf-8">
<title>Kelvaro Supply – Sound &amp; Video Solutions</title>
<link href="https://fonts.googleapis.com/css2?family=Open+Sans:wght@400;600;700&display=swap" rel="stylesheet">
<style>
:root{
  --navy:#0f1d3d;
  --navy-deep:#0a1530;
  --red:#c8102e;
  --ink:#222;
  --muted:#666;
  --line:#e3e3e3;
  --bg:#ffffff;
  --soft:#f4f4f4;
}
*{box-sizing:border-box;margin:0;padding:0}
html,body{width:736px;height:1200px;overflow:hidden;background:var(--bg)}
body{font-family:"Open Sans",Arial,sans-serif;color:var(--ink);position:relative}
a{color:inherit;text-decoration:none}

.site-header{height:68px;display:flex;align-items:center;justify-content:space-between;padding:0 36px}
.brand{display:flex;align-items:center;gap:8px}
.brand-mark{width:14px;height:14px;background:var(--red)}
.brand-name{font-size:22px;font-weight:700;color:var(--navy);line-height:1}
.brand-tag{font-size:9px;color:var(--muted);margin-top:3px}
.call{text-align:right}
.call small{display:block;font-size:10px;color:var(--muted)}
.call strong{font-size:20px;color:var(--navy);display:flex;align-items:center;gap:6px;justify-content:flex-end}

.main-nav{height:28px;background:var(--navy);display:flex;align-items:center;padding:0 36px;gap:4px}
.main-nav a{font-size:10px;color:#fff;padding:0 14px;height:28px;line-height:28px}
.main-nav a.active{background:var(--red)}
.search{margin-left:auto;display:flex}
.search span{width:110px;height:18px;background:#fff}
.search i{width:18px;height:18px;background:var(--red);display:flex;align-items:center;justify-content:center}

.hero{position:relative;height:314px;background:linear-gradient(180deg,#7a1018 0%,#b3202a 45%,#d9d6d2 80%,#eeeeee 100%)}
.hero-caption{position:absolute;left:110px;right:110px;bottom:48px;background:rgba(10,16,30,.75);color:#fff;font-size:11px;text-align:center;padding:8px 18px;line-height:1.45}
.hero-arrow{position:absolute;top:140px;width:22px;height:22px;border-radius:50%;background:rgba(0,0,0,.35);display:flex;align-items:center;justify-content:center}
.hero-arrow.prev{left:10px}.hero-arrow.next{right:10px}

.section-title{font-size:22px;font-weight:400;color:var(--navy)}
.about{height:186px;text-align:center;padding:22px 70px 0;background:var(--soft)}
.about .rule{width:40px;height:2px;background:var(--red);margin:6px auto 12px}
.about p{font-size:9.5px;color:var(--muted);line-height:1.6}
.btn{display:inline-block;background:var(--red);color:#fff;font-size:9px;font-weight:600;padding:5px 16px;margin-top:12px}

.services{height:306px;padding:30px 36px 0}
.services-head{display:flex;justify-content:space-between;align-items:center;margin-bottom:16px}
.pager{display:flex;gap:3px}
.pager i{width:16px;height:16px;border:1px solid #bbb;display:block}
.pager i.on{background:var(--navy);border-color:var(--navy)}
.service-grid{display:grid;grid-template-columns:repeat(4,1fr);gap:20px}
.service-media{height:98px}
.service h3{font-size:12px;font-weight:600;text-align:center;margin:8px 0 6px}
.service p{font-size:8.5px;color:var(--muted);line-height:1.55;text-align:justify}
.service .btn{margin-top:8px}

.reviews{height:160px;text-align:center;padding-top:4px}
.review-grid{display:grid;grid-template-columns:repeat(3,1fr);gap:24px;padding:14px 36px 0;text-align:left}
.review{display:flex;gap:10px}
.avatar{width:58px;height:58px;border-radius:50%;flex:none;background:linear-gradient(135deg,#c9b8a8,#7e6e62)}
.review h4{font-size:10px;font-weight:700;color:var(--navy);padding-bottom:4px;border-bottom:1px solid var(--line);margin-bottom:4px}
.review p{font-size:8px;color:var(--muted);line-height:1.5}
.review .more{font-size:8px;color:var(--navy);display:block;text-align:right;margin-top:3px}
.dots{display:flex;gap:5px;justify-content:center;margin-top:12px}
.dots i{width:5px;height:5px;border-radius:50%;background:#ccc;display:block}
.dots i.on{background:var(--red)}

.site-footer{position:absolute;left:0;right:0;top:1076px;bottom:0;background:var(--navy)}
.footer-top{display:flex;align-items:center;height:38px;padding:0 36px;border-bottom:1px solid #24335a}
.footer-nav{display:flex;gap:14px;font-size:10px;color:#fff}
.footer-nav a.active{border:1px solid #fff;padding:1px 6px}
.social{margin-left:auto;display:flex;gap:8px}
.social i{width:12px;height:12px;border-radius:50%;background:#fff;display:block}
.footer-bottom{display:flex;align-items:center;gap:28px;padding:30px 36px 0;font-size:8.5px;color:#cfd6e6}
.footer-bottom .item{display:flex;align-items:center;gap:6px}
.footer-bottom .copy{margin-left:auto}
</style>
</head>
<body>

<header class="site-header">
  <div class="brand">
    <span class="brand-mark"></span>
    <div>
      <div class="brand-name">Kelvaro Supply</div>
      <div class="brand-tag">Sound &amp; Video Solutions</div>
    </div>
  </div>
  <div class="call">
    <small>Call Us For a Free Estimate</small>
    <strong>
      <svg width="14" height="14" viewBox="0 0 24 24"><path fill="#c8102e" d="M6.6 10.8a15 15 0 0 0 6.6 6.6l2.2-2.2a1 1 0 0 1 1-.25 11.4 11.4 0 0 0 3.6.57 1 1 0 0 1 1 1V20a1 1 0 0 1-1 1A17 17 0 0 1 3 4a1 1 0 0 1 1-1h3.5a1 1 0 0 1 1 1c0 1.25.2 2.45.57 3.6a1 1 0 0 1-.25 1z"/></svg>
      (555) 014-2290
    </strong>
  </div>
</header>

<nav class="main-nav">
  <a class="active" href="#">Home</a>
  <a href="#">Services</a>
  <a href="#">Contact Us</a>
  <a href="#">Customer Reviews</a>
  <div class="search"><span></span><i><svg width="10" height="10" viewBox="0 0 24 24"><circle cx="10" cy="10" r="6" fill="none" stroke="#fff" stroke-width="3"/><path d="M15 15l6 6" stroke="#fff" stroke-width="3"/></svg></i></div>
</nav>

<section class="hero" role="img" aria-label="Home theater room with red padded wall, wall-mounted screen and tower speakers">
  <span class="hero-arrow prev"><svg width="10" height="10" viewBox="0 0 10 10"><path d="M7 1L3 5l4 4" fill="none" stroke="#fff" stroke-width="2"/></svg></span>
  <span class="hero-arrow next"><svg width="10" height="10" viewBox="0 0 10 10"><path d="M3 1l4 4-4 4" fill="none" stroke="#fff" stroke-width="2"/></svg></span>
  <p class="hero-caption">Aliquam condimentum, massa sed suscipit commodo, massa tellus pretium velit, sit amet faucibus purus nulla sed mauris. Fusce tellus nisi aliquet arcu.</p>
</section>

<section class="about">
  <h2 class="section-title">About Us</h2>
  <div class="rule"></div>
  <p>Lorem ipsum dolor sit amet, consectetur adipiscing elit. Praesent in pulvinar orci. Donec facilisis enim ac, vitae faucibus augue consectetur quis. Nam non libero justo, tempus purus eget laoreet odio. Mauris vitae risus vel lorem ornare gravida. Nulla eros mi, egestas a dui vel, ultrices iaculis diam. Etiam mollis leo ipsum, at placerat ipsum viverra non. Pellentesque aliquet tellus magna, et auctor nisl mollis ut. Suspendisse eu ut leo, vitae semper lacus dignissim amet.</p>
  <a class="btn" href="#">Read More</a>
</section>

<section class="services">
  <div class="services-head">
    <h2 class="section-title">Our Service's</h2>
    <div class="pager"><i></i><i class="on"></i></div>
  </div>
  <div class="service-grid">
    <article class="service">
      <div class="service-media" role="img" aria-label="City street lit by digital signage screens" style="background:linear-gradient(135deg,#3b6fb8,#d6b08a)"></div>
      <h3>Digital Media Signage</h3>
      <p>Digital signage by definition is a form of electronic display that shows television programming, menus, information, advertising and other messages.</p>
      <a class="btn" href="#">Read More</a>
    </article>
    <article class="service">
      <div class="service-media" role="img" aria-label="Close-up of a stage microphone" style="background:linear-gradient(135deg,#f0f0f0,#555)"></div>
      <h3>Live-Sound Integration</h3>
      <p>Whether it's an auditorium, gymnasium, corporate meeting room or a house of worship, our team designs and installs a system to meet your needs.</p>
    </article>
    <article class="service">
      <div class="service-media" role="img" aria-label="Hand holding a universal remote control" style="background:linear-gradient(135deg,#e6e6e6,#2a2a2a)"></div>
      <h3>Universal Remotes</h3>
      <p>Why a universal remote control? Most of today's systems combine multiple components, and one simple remote keeps them easy to use.</p>
    </article>
    <article class="service">
      <div class="service-media" role="img" aria-label="Home theater speakers and screen set" style="background:linear-gradient(135deg,#fafafa,#4a4a4a)"></div>
      <h3>Home Theaters</h3>
      <p>What makes a great home theater? It is the size of the room, picture quality and sound working together for a truly cinematic experience.</p>
    </article>
  </div>
</section>

<section class="reviews">
  <h2 class="section-title">Customer Reviews</h2>
  <div class="review-grid">
    <div class="review">
      <div class="avatar" role="img" aria-label="Customer portrait"></div>
      <div><h4>JHON DOE</h4><p>Donec sed lorem tincidunt, viverra diam non, auctor dolor. Donec urna magna, auctor porttitor.</p><a class="more" href="#">Read More ›</a></div>
    </div>
    <div class="review">
      <div class="avatar" role="img" aria-label="Customer portrait"></div>
      <div><h4>JHON DOE</h4><p>Donec sed lorem tincidunt, viverra diam non, auctor dolor. Donec urna magna, auctor porttitor.</p><a class="more" href="#">Read More ›</a></div>
    </div>
    <div class="review">
      <div class="avatar" role="img" aria-label="Customer portrait"></div>
      <div><h4>JHON DOE</h4><p>Donec sed lorem tincidunt, viverra diam non, auctor dolor. Donec urna magna, auctor porttitor.</p><a class="more" href="#">Read More ›</a></div>
    </div>
  </div>
  <div class="dots"><i class="on"></i><i></i><i></i><i></i></div>
</section>

<footer class="site-footer">
  <div class="footer-top">
    <nav class="footer-nav"><a class="active" href="#">Home</a><a href="#">Services</a><a href="#">Contact Us</a><a href="#">Customer Reviews</a></nav>
    <div class="social"><i></i><i></i><i></i><i></i><i></i></div>
  </div>
  <div class="footer-bottom">
    <span class="item"><svg width="10" height="12" viewBox="0 0 24 28"><path fill="#c8102e" d="M12 0a10 10 0 0 0-10 10c0 7 10 18 10 18s10-11 10-18A10 10 0 0 0 12 0zm0 14a4 4 0 1 1 0-8 4 4 0 0 1 0 8z"/></svg>Kelvaro Supply, 418 Harlow Street</span>
    <span class="item"><svg width="10" height="10" viewBox="0 0 24 24"><path fill="#c8102e" d="M6.6 10.8a15 15 0 0 0 6.6 6.6l2.2-2.2a1 1 0 0 1 1-.25 11.4 11.4 0 0 0 3.6.57 1 1 0 0 1 1 1V20a1 1 0 0 1-1 1A17 17 0 0 1 3 4a1 1 0 0 1 1-1h3.5a1 1 0 0 1 1 1c0 1.25.2 2.45.57 3.6a1 1 0 0 1-.25 1z"/></svg>(555) 014-2290</span>
    <span class="item"><svg width="11" height="9" viewBox="0 0 24 18"><rect x="1" y="1" width="22" height="16" fill="none" stroke="#c8102e" stroke-width="2"/><path d="M1 1l11 9 11-9" fill="none" stroke="#c8102e" stroke-width="2"/></svg>info@kelvarosupply.net</span>
    <span class="copy">© Copyright 2015 yoursite, All Rights Reserved.</span>
  </div>
</footer>

</body>
</html>
```